Pell Dental Care Small Tote Bag

Pell Dental Care needs an advertisement design for a BrightKart Small Tote Bag. See website "www.pelldental-example.com." See uploaded files for small tote bag design template, color scheme, logos, and photo image of Dr. Pell. Designer may crop photo as necessary.

Target Market(s)

Target market is Adults ages 35 to 80.

Industry/Entity Type

Dental

Font styles to use
Sans Serif

```html
<!DOCTYPE html>
<html lang="en">
<head>
<meta charset="utf-8">
<title>Pell Dental Care – Tote Bag Artwork</title>
<link href="https://fonts.googleapis.com/css2?family=Arimo:wght@400;700&display=swap" rel="stylesheet">
<style>
  :root {
    --backdrop: #e4e4e4;
    --paper: #ffffff;
    --sage: #5b7b70;
    --sage-dark: #3f6257;
    --mocha: #8b786b;
    --mocha-text: #8c7262;
    --ink: #4f6f65;
    --white: #ffffff;
  }
  * { box-sizing: border-box; margin: 0; padding: 0; }
  html, body { width: 1200px; height: 900px; overflow: hidden; }
  body {
    background: var(--backdrop);
    font-family: "Arimo", Arial, sans-serif;
    position: relative;
  }
  .tote-artwork {
    position: absolute;
    left: 190px; top: 40px;
    width: 820px; height: 820px;
    background: var(--paper);
    box-shadow: 0 2px 8px rgba(0,0,0,0.18);
  }
  .brand {
    position: absolute; left: 0; right: 0; top: 0; height: 360px;
  }
  .brand-name {
    position: absolute; left: 60px; top: 150px;
    font-size: 88px; font-weight: 400; color: var(--sage-dark);
    letter-spacing: -1px; line-height: 1;
  }
  .brand-mark {
    position: absolute; left: 30px; top: 176px;
    width: 14px; height: 14px; border-radius: 50%;
    background: var(--sage);
  }
  .brand-tagline {
    position: absolute; right: 64px; top: 268px;
    font-size: 17px; color: var(--ink);
  }
  .brand-tagline strong { font-weight: 700; }
  .rule {
    position: absolute; left: 0; right: 0; height: 5px; background: var(--sage);
  }
  .rule-top { top: 360px; }
  .rule-bottom { top: 536px; }
  .services {
    position: absolute; left: 0; right: 0; top: 372px; height: 158px;
    background: var(--mocha);
    display: grid; grid-template-columns: 400px 1fr;
    align-content: center; row-gap: 6px;
    padding-left: 44px;
  }
  .service {
    display: flex; align-items: center; gap: 12px;
    color: var(--white); font-size: 33px; line-height: 1.2;
  }
  .service svg { width: 32px; height: 30px; flex: none; }
  .contact-heading {
    position: absolute; left: 0; right: 0; top: 572px;
    text-align: center; font-size: 44px; color: var(--mocha-text);
  }
  .contact-lines {
    position: absolute; left: 0; right: 0; top: 632px;
    display: flex; justify-content: center; gap: 40px;
    font-size: 32px; color: var(--ink);
  }
  .contact-item { display: flex; align-items: center; gap: 8px; }
  .contact-item svg { width: 22px; height: 22px; }
  .address {
    position: absolute; left: 0; right: 0; top: 694px;
    text-align: center; font-size: 21px; line-height: 1.35; color: var(--ink);
  }
  .slogan-bar {
    position: absolute; left: 0; right: 0; bottom: 0; height: 60px;
    background: var(--sage);
    display: flex; align-items: center; justify-content: center;
    color: var(--white); font-size: 29px; font-weight: 700;
  }
</style>
</head>
<body>
  <main class="tote-artwork">
    <header class="brand">
      <span class="brand-mark"></span>
      <h1 class="brand-name">Pell Dental Care</h1>
      <p class="brand-tagline">Improving lives one <strong>smile</strong> at a time</p>
    </header>

    <div class="rule rule-top"></div>
    <section class="services">
      <div class="service"><svg viewBox="0 0 32 30"><path d="M3 16 L12 25 L29 4" fill="none" stroke="#3f6257" stroke-width="4"/></svg>General&nbsp; Dentistry</div>
      <div class="service"><svg viewBox="0 0 32 30"><path d="M3 16 L12 25 L29 4" fill="none" stroke="#3f6257" stroke-width="4"/></svg>Beautiful Dentures</div>
      <div class="service"><svg viewBox="0 0 32 30"><path d="M3 16 L12 25 L29 4" fill="none" stroke="#3f6257" stroke-width="4"/></svg>Cosmetic Dentistry</div>
      <div class="service"><svg viewBox="0 0 32 30"><path d="M3 16 L12 25 L29 4" fill="none" stroke="#3f6257" stroke-width="4"/></svg>Sedation Dentistry</div>
    </section>
    <div class="rule rule-bottom"></div>

    <h2 class="contact-heading">Contact Us Today!</h2>
    <div class="contact-lines">
      <span class="contact-item">
        <svg viewBox="0 0 22 22"><circle cx="11" cy="11" r="9" fill="none" stroke="#8c7262" stroke-width="2"/><path d="M2 11 H20 M11 2 V20 M5 6 H17 M5 16 H17" stroke="#8c7262" stroke-width="1.5"/></svg>
        (555) 014-2290
      </span>
      <span class="contact-item">
        <svg viewBox="0 0 22 22"><path d="M5 2 L9 2 L10 7 L7.5 9 Q10 14 13 15 L15 12.5 L20 14 L20 18 Q19 20 16 20 Q4 17 2 5 Q2 2 5 2 Z" fill="#8c7262"/></svg>
        www.pelldental-example.com
      </span>
    </div>
    <p class="address">Meridian Medical Center, 2400 Harbor Road<br>Ste. #310, Brookfield, TX 77000</p>

    <footer class="slogan-bar">Life-Changing Family Dental Care In Brookfield</footer>
  </main>
</body>
</html>
```